Business cards for a fun web development agency

Hi,I am building a web development agency. You can read about it on the website http://kite-loft.examplehost.com. Basically, I want to focus on free and open source products and stay as far away from the corporate business feeling as possible. I want to build a community so I want the business card to feel fun and approachable (at the risk of professional if need be). I am uploading some of my image assets in various file formats. Feel free to use them or make your own if you want just keeping in theme with the website.
Industry/Entity Type
Building
Contact Information for Business Card
Company Name: Boat ShedWebsite: www.kiteloftdev.example (it's currently in alpha on http://kite-loft.examplehost.com if you want to see the them we are trying to capture)My name is: Banner B. SchaferMy email: banner@boatsheddev.comMy phone: 0431 587 904
Look and feel

```html
<!DOCTYPE html>
<html lang="en">
<head>
<meta charset="utf-8">
<title>Kite Loft – Business Cards</title>
<link rel="stylesheet" href="https://fonts.googleapis.com/css2?family=Open+Sans:wght@400;600;700&family=Raleway:wght@500&display=swap">
<style>
  :root {
    --backdrop: #3a3a3c;
    --sky-top: #3f93c6;
    --sky-bottom: #7fc0dc;
    --horizon: #2d5d96;
    --water-top: #9ed4d8;
    --water-bottom: #84c2c9;
    --ink: #2b4d7e;
    --ink-soft: #3f6a93;
    --scene-light: #a6d6e2;
    --scene-mid: #6fa6cf;
    --scene-deep: #4f7fb4;
    --fish: rgba(70, 120, 140, 0.25);
  }
  * { box-sizing: border-box; margin: 0; padding: 0; }
  html, body {
    width: 1200px; height: 852px; overflow: hidden;
    background: var(--backdrop);
    font-family: "Open Sans", sans-serif;
  }
  .stage {
    position: relative; width: 1200px; height: 852px;
    display: flex; align-items: center; justify-content: center; gap: 40px;
  }
  .card {
    position: relative; width: 540px; height: 315px;
    border-radius: 24px; overflow: hidden;
    background: linear-gradient(180deg, var(--water-top), var(--water-bottom));
    box-shadow: 0 12px 30px rgba(0,0,0,0.45);
  }
  .sky-scene {
    position: absolute; left: 0; top: 0; width: 100%; height: 72px;
    background: linear-gradient(180deg, var(--sky-top), var(--sky-bottom));
  }
  .horizon {
    position: absolute; left: 0; width: 100%; height: 4px;
    background: var(--horizon);
  }
  .fish-school {
    position: absolute; border-radius: 50%;
    background: radial-gradient(ellipse at center, var(--fish), rgba(70,120,140,0) 70%);
  }
  .wordmark {
    position: absolute; display: flex; align-items: center; gap: 12px;
    font-family: "Raleway", sans-serif; font-weight: 500;
    color: var(--ink); letter-spacing: 2px; text-transform: uppercase;
    white-space: nowrap;
  }
  .wordmark .dot { border-radius: 50%; background: var(--ink); }

  /* Front */
  .card-front .horizon { top: 72px; }
  .card-front .wordmark { left: 50%; top: 140px; transform: translateX(-50%); font-size: 50px; }
  .card-front .wordmark .dot { width: 46px; height: 46px; }
  .card-front .fish-school { left: 150px; top: 220px; width: 220px; height: 70px; }

  /* Back */
  .card-back .sky-scene { height: 108px; background: linear-gradient(180deg, var(--sky-bottom), var(--water-top)); }
  .card-back .horizon { top: 108px; }
  .card-back .wordmark { left: 30px; top: 62px; font-size: 32px; gap: 8px; }
  .card-back .wordmark .dot { width: 28px; height: 28px; }
  .pier-scene {
    position: absolute; right: 0; top: 0; width: 210px; height: 100%;
    background: linear-gradient(180deg, var(--scene-light) 0%, var(--scene-mid) 45%, var(--scene-deep) 100%);
  }
  .identity { position: absolute; left: 36px; top: 140px; color: var(--ink); }
  .identity .name { font-weight: 700; font-size: 19px; }
  .identity .role { font-size: 12px; color: var(--ink-soft); margin-top: 2px; padding-left: 12px; }
  .contact-list { position: absolute; left: 36px; top: 210px; list-style: none; color: var(--ink); font-size: 15px; }
  .contact-list li { display: flex; align-items: center; gap: 12px; height: 26px; white-space: nowrap; }
  .contact-list svg { width: 14px; height: 14px; fill: var(--ink); flex: none; }
</style>
</head>
<body>
<main class="stage">

  <section class="card card-front" aria-label="Business card front">
    <div class="sky-scene" role="img" aria-label="Illustrated sky with clouds and seagulls"></div>
    <div class="horizon"></div>
    <div class="fish-school" role="img" aria-label="Faint school of fish under the water"></div>
    <div class="wordmark"><span class="dot"></span>Kite Loft</div>
  </section>

  <section class="card card-back" aria-label="Business card back">
    <div class="sky-scene"></div>
    <div class="horizon"></div>
    <div class="pier-scene" role="img" aria-label="Illustration of a blue shed on a jetty with sun rays"></div>
    <div class="wordmark"><span class="dot"></span>Kite Loft</div>
    <div class="identity">
      <p class="name">Corwin T. Aldous</p>
      <p class="role">Managing Director</p>
    </div>
    <ul class="contact-list">
      <li>
        <svg viewBox="0 0 16 16" aria-hidden="true"><path d="M3 1l3 3-1.5 2a9 9 0 0 0 5.5 5.5L12 10l3 3-2 2C6 15 1 10 1 3z"/></svg>
        0431 587 904
      </li>
      <li>
        <svg viewBox="0 0 16 16" aria-hidden="true"><path d="M1 3h14v10H1z M1 3l7 6 7-6" stroke="#9ed4d8" stroke-width="1.2"/></svg>
        corwin@kiteloftdev.example
      </li>
      <li>
        <svg viewBox="0 0 16 16" aria-hidden="true"><circle cx="8" cy="8" r="7"/><path d="M1 8h14M8 1c-3 4-3 10 0 14M8 1c3 4 3 10 0 14" stroke="#9ed4d8" stroke-width="1" fill="none"/></svg>
        www.kiteloftdev.example
      </li>
    </ul>
  </section>

</main>
</body>
</html>
```